Business Card Design Project

Doctor, Pain Management. Need a new business card design with appointment info on the back. New address is 18 Corvell Road, Suite 304, Brisdale, NJ 07391. Right now I believe the rest of the information is staying the same.

```html
<!DOCTYPE html>
<html lang="en">
<head>
<meta charset="utf-8">
<title>Steadfast Pain Management – Business Card</title>
<link rel="stylesheet" href="https://fonts.googleapis.com/css2?family=Tinos:wght@400;700&family=Montserrat:wght@400&display=swap">
<style>
  :root {
    --yellow: #e9e83a;
    --black: #050505;
    --white: #f1f1f1;
    --ink: #111111;
    --stage: #2b2b2b;
  }
  * { margin: 0; padding: 0; box-sizing: border-box; }
  html, body { width: 1200px; height: 923px; overflow: hidden; background: var(--stage); }
  body { position: relative; font-family: "Tinos", "Times New Roman", serif; color: var(--ink); }

  .card { position: absolute; top: 313px; width: 520px; height: 297px; overflow: hidden; }
  .card-back { left: 50px; background: var(--white); }
  .card-front { left: 630px; background: var(--black); }

  /* Back: appointment side */
  .appt-header {
    position: absolute; left: 0; top: 0; width: 100%; height: 48px;
    background: var(--yellow); border-bottom: 5px solid var(--black);
    display: flex; align-items: center; justify-content: space-between; padding: 0 18px;
    font-size: 17px;
  }
  .appt-header .label { font-weight: 700; }
  .appt-title { font-size: 30px; font-weight: 700; }
  .appt-body { position: absolute; left: 28px; right: 28px; top: 70px; font-size: 19px; }
  .field { display: flex; align-items: flex-end; gap: 8px; margin-bottom: 16px; }
  .field .rule { flex: 1; border-bottom: 1.5px solid var(--ink); height: 18px; }
  .days { display: flex; justify-content: space-between; margin-bottom: 18px; }
  .day::before {
    content: ""; display: inline-block; width: 13px; height: 13px;
    border: 1.5px solid var(--ink); margin-right: 4px; vertical-align: -1px;
  }
  .field-row { display: flex; gap: 24px; }
  .field-row .field { flex: 1; }
  .appt-note { text-align: center; font-weight: 700; font-size: 16px; line-height: 1.2; margin-top: 4px; }
  .appt-footer {
    position: absolute; left: 0; bottom: 0; width: 100%; height: 44px;
    background: var(--black); color: var(--yellow);
    font-family: "Montserrat", Arial, sans-serif; font-size: 15px;
    display: flex; align-items: center; padding-left: 28px;
  }

  /* Front: practice side */
  .front-panels { position: absolute; inset: 0; }
  .practice-name {
    position: absolute; left: 0; right: 0; top: 22px; text-align: center;
    color: var(--yellow); font-size: 40px; font-weight: 400; line-height: 1; white-space: nowrap;
  }
  .name-rule { position: absolute; left: 90px; right: 52px; top: 72px; border-top: 1.5px solid var(--white); }
  .doctor { position: absolute; left: 150px; right: 40px; top: 80px; text-align: center; line-height: 1.15; }
  .doctor-name { color: var(--white); font-weight: 700; font-size: 26px; }
  .doctor-cred { color: var(--yellow); font-size: 19px; }
  .front-contact {
    position: absolute; left: 42px; bottom: 26px; font-size: 19px; line-height: 1.25; font-weight: 700;
  }
  .front-address {
    position: absolute; right: 16px; top: 180px; text-align: right; font-size: 16px; line-height: 1.3;
    font-style: normal;
  }
  .front-address .street { font-size: 17px; }
  .front-address .city { font-size: 15px; }
</style>
</head>
<body>

<section class="card card-back" aria-label="Appointment card">
  <header class="appt-header">
    <span><span class="label">P:</span> (973) 555-0148</span>
    <span class="appt-title">Appointment</span>
    <span><span class="label">F:</span> (973) 555.0162</span>
  </header>
  <div class="appt-body">
    <div class="field"><span>For:</span><span class="rule"></span></div>
    <div class="days">
      <span class="day">Mon</span><span class="day">Tue</span><span class="day">Wed</span><span class="day">Thu</span><span class="day">Fri</span><span class="day">Sat</span><span class="day">Sun</span>
    </div>
    <div class="field-row">
      <div class="field"><span>Date:</span><span class="rule"></span></div>
      <div class="field"><span>Time:</span><span class="rule"></span></div>
    </div>
    <p class="appt-note">If you are unable to keep this appointment,<br>please call 24 hours ahead.</p>
  </div>
  <footer class="appt-footer">www.steadfastpm.com</footer>
</section>

<section class="card card-front" aria-label="Business card front">
  <svg class="front-panels" width="520" height="297" viewBox="0 0 520 297">
    <polygon points="0,172 250,172 370,297 0,297" fill="var(--yellow)"/>
    <polygon points="250,172 520,112 520,297 370,297" fill="var(--white)"/>
  </svg>
  <h1 class="practice-name">Steadfast Pain Management</h1>
  <div class="name-rule"></div>
  <div class="doctor">
    <div class="doctor-name">Dr. Meilin Harrow</div>
    <div class="doctor-cred">M.D., Ph.D.</div>
  </div>
  <address class="front-address">
    <div>office@steadfastpm.com</div>
    <div class="street">18 Corvell Road, Suite 304</div>
    <div class="city">Brisdale, NJ 07391</div>
  </address>
  <div class="front-contact">
    <div>P : (973) 555-0148</div>
    <div>F : (973) 555.0162</div>
    <div>www.steadfastpm.com</div>
  </div>
</section>

</body>
</html>
```